Nanny Share Ecommerce Website for Finding Childcare and Parents who need Childcare BrightPramHub.net

Our company needs an ecommerce website (BrightPramHub.net) for a US subscription based service strictly for nanny sharing that connects families and caregivers. The website would allow families to connect with one another as well as to search for nannies. The service would be searchable for other families by location (by radius or zip code), children demographic (age range/gender/special needs), days of week or times, after school care, school closure days (holidays), etc. The service would also be searchable for nannies based on gender, provider age range, years experience, language, hourly rate, transportation available, certification (CPR first aid), education etc. The search fields would be searchable and sortable and allow to connect with the provider (after paying subscription fee). The service would be similar to tendlyfolk.net in that it would allow for families and caregivers to post photos as well as a short bio of the themselves. There would also be a feedback/star rating mechanism to rate caregivers who have performed work for families (viewable to public). The service would be free for nannies to post their bios and only a subscription based service for families to connect with other families or with caregivers (able to view bio but need service to connect). There will be a short bio on the benefits of nanny sharing (reduced cost, increased flexibility for parents, reduced illness, increased socialization with other children vs. sole nanny), as well as Q&A section with best practices.

Target Market(s)

Families, Nannies

Industry/Entity Type

Childcare

Logo Text

Bright Pram Hub

Coding

Coded - Design and coding required

Number of Pages Required

5+ page

Requirements
Must have
• Searchable (need to be able to search for families as well as nannies), responsive, functional, easy to use, add value to families and nannies. Needs to be able to collect payment for subscription.
Nice to have
• Optimized for mobile, SEO optimized

```html
<!DOCTYPE html>
<html lang="en">
<head>
<meta charset="utf-8">
<title>Bright Pram Hub – Nanny Sharing</title>
<link rel="stylesheet" href="https://fonts.googleapis.com/css2?family=Poppins:ital,wght@0,300;0,400;0,500;0,600;1,300;1,400&display=swap">
<style>
:root{
  --red:#f5505a;
  --red-dark:#e8434d;
  --ink:#222;
  --text:#555;
  --muted:#8a8a8a;
  --line:#dcdcdc;
  --soft:#f1f1f1;
  --white:#fff;
  --dark:#2b2b2b;
}
*{box-sizing:border-box;margin:0;padding:0}
html,body{width:1200px;height:3309px;overflow:hidden}
body{font-family:"Poppins",sans-serif;color:var(--text);background:var(--white);position:relative}
.abs{position:absolute}

/* header */
.site-header{position:absolute;left:0;top:0;width:1200px;height:77px;background:var(--white)}
.brand{position:absolute;left:161px;top:26px;font-size:17px;font-weight:400;color:var(--ink)}
.main-nav{position:absolute;left:366px;top:32px;display:flex;gap:28px;font-size:11px;font-weight:500;color:var(--ink)}
.main-nav .active{color:var(--red)}
.search{position:absolute;left:770px;top:25px;width:183px;height:28px;border:1px solid var(--line);border-radius:14px;font-size:10px;color:#aaa;padding:7px 14px}
.search svg{position:absolute;right:12px;top:8px}
.btn-login{position:absolute;left:973px;top:25px;width:64px;height:28px;border-radius:14px;background:var(--red);color:var(--white);font-size:10px;font-weight:500;text-align:center;line-height:28px}

/* hero */
.hero{position:absolute;left:0;top:77px;width:1200px;height:503px;background:linear-gradient(100deg,#e9e6e2 0%,#dcd8d2 40%,#c9b6a4 65%,#a98466 100%)}
.hero h1{position:absolute;left:161px;top:128px;font-size:44px;font-weight:400;line-height:54px;color:var(--ink)}
.hero p{position:absolute;left:161px;top:250px;width:380px;font-size:13px;line-height:22px;color:var(--ink)}
.btn-pill{display:inline-block;background:var(--red);color:var(--white);border-radius:22px;font-weight:500;text-align:center}
.hero .btn-pill{position:absolute;left:161px;top:338px;width:122px;height:42px;line-height:42px;font-size:11px}
.hero-dots{position:absolute;left:1143px;top:245px;display:flex;flex-direction:column;gap:8px}
.hero-dots span{width:14px;height:14px;border-radius:50%;background:var(--white);opacity:.8}
.hero-dots span:nth-child(2){opacity:1;width:16px;height:16px;margin-left:-1px}

/* search */
.finder{position:absolute;left:0;top:580px;width:1200px;height:313px;background:var(--soft)}
.finder-box{position:absolute;left:132px;top:38px;width:936px;height:234px;border:2px solid var(--red)}
.finder h2{position:absolute;left:0;top:20px;width:1200px;text-align:center;font-size:27px;font-weight:400;color:var(--ink)}
.finder h2 span{background:var(--soft);padding:0 22px}
.field{position:absolute;width:210px}
.field label{display:block;font-size:11px;color:var(--ink);margin-bottom:7px}
.field .input{height:32px;background:var(--white);border:1px solid var(--line);font-size:10px;color:#999;padding:8px 8px;position:relative}
.field .input.select::after{content:"";position:absolute;right:0;top:0;width:26px;height:30px;border-left:1px solid var(--line);background:#f7f7f7}
.field .input.select::before{content:"";position:absolute;right:9px;top:13px;border:4px solid transparent;border-top-color:#777;z-index:2}
.finder .btn-pill{position:absolute;left:516px;top:218px;width:168px;height:36px;line-height:36px;font-size:11px}

/* cards */
.audiences{position:absolute;left:0;top:893px;width:1200px;height:614px}
.audiences h2{position:absolute;top:28px;font-size:25px;font-weight:400;color:var(--ink)}
.card{position:absolute;width:428px;height:223px;border:1px solid #e4e4e4;background:var(--white)}
.card .photo{position:absolute;left:10px;top:10px;width:200px;height:201px}
.card h3{position:absolute;left:222px;top:24px;width:190px;font-size:14px;font-weight:400;line-height:24px;color:var(--ink);text-transform:uppercase}
.card p{position:absolute;left:222px;top:78px;width:190px;font-size:10px;line-height:19px;color:var(--text)}
.card .btn-outline{position:absolute;left:222px;top:170px;width:82px;height:30px;border:1px solid var(--red);border-radius:15px;font-size:10px;color:var(--red);text-align:center;line-height:28px}

/* reviews */
.reviews{position:absolute;left:0;top:1507px;width:1200px;height:386px;background:var(--soft)}
.reviews .notch{position:absolute;left:560px;top:0}
.reviews h2{position:absolute;left:0;top:60px;width:1200px;text-align:center;font-size:24px;font-weight:400;color:var(--ink)}
.avatar{position:absolute;left:256px;top:153px;width:124px;height:124px;border-radius:50%;background:radial-gradient(circle at 50% 45%,#d9a882,#9a6b4c 70%,#7aa3c6 71%);border:4px solid var(--white)}
.quote{position:absolute;left:410px;top:138px;width:580px;font-size:12.5px;line-height:25px;font-style:italic;font-weight:300;color:var(--ink)}
.quote .mark{color:var(--red);font-weight:600;font-style:normal}
.stars{position:absolute;left:410px;top:278px;color:#f4b400;font-size:13px;letter-spacing:1px}
.reviewer{position:absolute;left:412px;top:302px;font-size:12px;font-weight:500;color:var(--ink)}
.dots{position:absolute;left:578px;top:340px;display:flex;gap:3px}
.dots span{width:13px;height:13px;border-radius:50%;background:#a9a9a9}
.dots span:nth-child(2){background:var(--red)}

/* benefits */
.benefits{position:absolute;left:0;top:1893px;width:1200px;height:534px;background:var(--red)}
.benefits .photo{position:absolute;left:0;top:42px;width:591px;height:492px;background:linear-gradient(120deg,#c49a72 0%,#e6d3bd 45%,#d7b8a0 70%,#8c6a53 100%)}
.benefits h2{position:absolute;left:618px;top:66px;font-size:26px;font-weight:400;color:var(--white)}
.benefit{position:absolute;left:620px;width:450px;color:var(--white)}
.benefit .icon{position:absolute;left:0;top:0;width:62px;height:62px;border:2px solid var(--white);border-radius:50%}
.benefit .icon svg{position:absolute;left:17px;top:17px}
.benefit h3{position:absolute;left:73px;top:-2px;width:370px;font-size:13.5px;font-weight:400;line-height:22px}
.benefit p{position:absolute;left:73px;top:22px;width:370px;font-size:9.5px;line-height:18px;opacity:.95}

/* faq */
.faq{position:absolute;left:0;top:2427px;width:1200px;height:492px}
.faq h2{position:absolute;left:0;top:60px;width:1200px;text-align:center;font-size:25px;font-weight:400;color:var(--ink)}
.faq-item{position:absolute;width:428px;height:50px;border:1px solid #e1e1e1;border-radius:25px;background:var(--white);font-size:12.5px;color:var(--ink);padding:0 24px;line-height:48px}
.faq-item::after{content:"+";position:absolute;right:22px;top:0;color:var(--red);font-size:20px;font-weight:400}
.faq-item.open{background:var(--red);border-color:var(--red);color:var(--white)}
.faq-item.open::after{content:"–";color:var(--white)}
.faq-item.open .tip{position:absolute;left:60px;bottom:-8px;border:8px solid transparent;border-bottom:0;border-top-color:var(--red)}
.faq-answer{position:absolute;left:161px;top:297px;width:428px;height:122px;border:1px solid #e1e1e1;border-radius:14px;padding:22px 28px;font-size:10px;line-height:20px;color:var(--ink)}

/* newsletter */
.newsletter{position:absolute;left:0;top:2919px;width:1200px;height:86px;background:var(--red)}
.newsletter h2{position:absolute;left:196px;top:26px;font-size:24px;font-weight:400;color:var(--white)}
.newsletter .field-email{position:absolute;left:457px;top:23px;width:520px;height:40px;border-radius:20px;background:var(--white);font-size:10px;color:#999;padding:12px 20px;overflow:hidden}
.newsletter .signup{position:absolute;right:0;top:0;width:78px;height:40px;background:var(--dark);color:var(--white);font-size:10px;font-weight:500;text-align:center;line-height:40px}

/* footer */
.site-footer{position:absolute;left:0;top:3005px;width:1200px;height:304px;background:var(--soft)}
.site-footer .brand{left:161px;top:30px}
.footer-about{position:absolute;left:161px;top:73px;width:200px;font-size:10.5px;line-height:25px;color:var(--ink)}
.footer-col{position:absolute;top:33px;font-size:10.5px;color:var(--ink)}
.footer-col h4{font-size:14px;font-weight:400;margin-bottom:10px}
.footer-col li{list-style:none;line-height:25px}
.social{position:absolute;left:164px;top:258px;display:flex;gap:14px;align-items:center}
.social .dot{width:18px;height:18px;border-radius:50%;background:var(--ink)}
.copyright{position:absolute;left:690px;top:262px;font-size:10.5px;color:var(--ink)}
.page-code{position:absolute;left:1070px;top:262px;font-size:10.5px;color:var(--ink)}
</style>
</head>
<body>

<header class="site-header">
  <div class="brand">Bright Pram Hub</div>
  <nav class="main-nav">
    <span class="active">HOME</span><span>ABOUT US</span><span>SERVICES</span><span>NEWS</span><span>FAQ</span><span style="margin-left:20px">CONTACT</span>
  </nav>
  <div class="search">Search
    <svg width="11" height="11" viewBox="0 0 11 11"><circle cx="4.5" cy="4.5" r="3.5" fill="none" stroke="#777" stroke-width="1.3"/><line x1="7" y1="7" x2="10" y2="10" stroke="#777" stroke-width="1.3"/></svg>
  </div>
  <div class="btn-login">LOGIN</div>
</header>

<section class="hero" role="img" aria-label="Photo of a smiling nanny playing with a toddler on a wooden floor">
  <h1>Welcome to<br>Bright Pram Hub</h1>
  <p>Find a shared nanny near you and split care costs with other local families you can trust.</p>
  <span class="btn-pill">FIND CARE</span>
  <div class="hero-dots"><span></span><span></span><span></span></div>
</section>

<section class="finder">
  <div class="finder-box"></div>
  <h2><span>Finding Nannies</span></h2>
  <div class="field" style="left:161px;top:84px"><label>Gender</label><div class="input select">Male</div></div>
  <div class="field" style="left:382px;top:84px"><label>Provider age range:</label><div class="input select">25 to 30</div></div>
  <div class="field" style="left:604px;top:84px"><label>Years experience</label><div class="input select">2 years experience</div></div>
  <div class="field" style="left:827px;top:84px"><label>Language</label><div class="input select">English</div></div>
  <div class="field" style="left:161px;top:154px"><label>Hourly Rate</label><div class="input select">$200</div></div>
  <div class="field" style="left:382px;top:154px"><label>Transportation Available</label><div class="input"></div></div>
  <div class="field" style="left:604px;top:154px"><label>Certification (CPR first aid)</label><div class="input select">Select</div></div>
  <div class="field" style="left:827px;top:154px"><label>Education</label><div class="input select">Select</div></div>
  <span class="btn-pill">SEARCH FOR NANNY</span>
</section>

<section class="audiences">
  <h2 style="left:161px">For The Family</h2>
  <h2 style="left:609px">For Nannies</h2>

  <article class="card" style="left:161px;top:93px">
    <div class="photo" role="img" aria-label="Photo of a young girl holding a parent's hand outdoors" style="background:linear-gradient(135deg,#7fa34a,#c8b07a 55%,#e6ddd0)"></div>
    <h3>Announces work &amp; explores candidates</h3>
    <p>Post your care needs, set your hours and review local nannies ready to share care.</p>
    <span class="btn-outline">Read More</span>
  </article>
  <article class="card" style="left:609px;top:93px">
    <div class="photo" role="img" aria-label="Photo of a caregiver drawing with two children at a table" style="background:linear-gradient(135deg,#d9cfc4,#b98f72 50%,#6e8fb5)"></div>
    <h3>Here you have your ideal job</h3>
    <p>Browse families near you, choose the schedule that fits and connect at no cost.</p>
    <span class="btn-outline">Read More</span>
  </article>
  <article class="card" style="left:161px;top:342px">
    <div class="photo" role="img" aria-label="Photo of a mother holding her baby" style="background:linear-gradient(135deg,#e8e2dc,#c79a7e 55%,#3d3a3a)"></div>
    <h3>Profiles evaluated by mothers</h3>
    <p>Every caregiver profile shows star ratings and notes from parents who hired them.</p>
    <span class="btn-outline">Read More</span>
  </article>
  <article class="card" style="left:609px;top:342px">
    <div class="photo" role="img" aria-label="Photo of two children playing with colourful toys" style="background:linear-gradient(135deg,#5e7d3f,#c2a25a 50%,#3f78b8)"></div>
    <h3>Create a free profile for</h3>
    <p>Add a photo and a short bio, list your skills and let families find you fast.</p>
    <span class="btn-outline">Read More</span>
  </article>
</section>

<section class="reviews">
  <svg class="notch" width="80" height="36" viewBox="0 0 80 36"><polygon points="0,0 80,0 40,36" fill="#fff"/></svg>
  <h2>Customer Reviews</h2>
  <div class="avatar" role="img" aria-label="Portrait of the reviewer"></div>
  <p class="quote"><span class="mark">“</span> Sharing a nanny with the family next door changed our weeks. Our kids play together every day, we split the cost fairly and the rating system helped us pick a caregiver we truly trust. Booking took minutes, the search filters were easy and the whole process felt calm and safe from start to finish for both of our families. <span class="mark">”</span></p>
  <div class="stars">★★★★★</div>
  <div class="reviewer">Dana Whitfield</div>
  <div class="dots"><span></span><span></span><span></span></div>
</section>

<section class="benefits">
  <div class="photo" role="img" aria-label="Photo of a nanny and two toddlers playing with a wooden dollhouse"></div>
  <h2>Benefits</h2>

  <div class="benefit" style="top:119px">
    <div class="icon"><svg width="28" height="28" viewBox="0 0 28 28"><circle cx="14" cy="14" r="12" fill="none" stroke="#fff" stroke-width="2"/><text x="14" y="20" text-anchor="middle" fill="#fff" font-family="Poppins,sans-serif" font-size="16" font-weight="500">$</text></svg></div>
    <h3>Reduced Cost</h3>
    <p>Two families share one nanny, so each pays less for the<br>same trusted, full day care.</p>
  </div>
  <div class="benefit" style="top:205px">
    <div class="icon"><svg width="28" height="28" viewBox="0 0 28 28"><circle cx="14" cy="14" r="12" fill="#fff"/><circle cx="11" cy="11" r="3" fill="#f5505a"/><circle cx="17.5" cy="11.5" r="2.5" fill="#f5505a"/><path d="M5.5 20c1-4 10-4 11 0z" fill="#f5505a"/><path d="M14 20c1-3 8-3 9 0z" fill="#f5505a"/></svg></div>
    <h3>Increased flexibility for parents</h3>
    <p>Swap hours and share pickups with a partner family when<br>plans change during the week.</p>
  </div>
  <div class="benefit" style="top:291px">
    <div class="icon"><svg width="28" height="28" viewBox="0 0 28 28"><circle cx="14" cy="14" r="12" fill="#fff"/><rect x="8" y="14" width="3" height="6" fill="#f5505a"/><rect x="12.5" y="11" width="3" height="9" fill="#f5505a"/><rect x="17" y="8" width="3" height="12" fill="#f5505a"/></svg></div>
    <h3>Reduced illness</h3>
    <p>Small groups in a home setting mean fewer germs than a<br>busy daycare centre.</p>
  </div>
  <div class="benefit" style="top:377px">
    <div class="icon"><svg width="28" height="28" viewBox="0 0 28 28"><circle cx="14" cy="14" r="12" fill="#fff"/><polyline points="7,19 11,14 15,16 21,9" fill="none" stroke="#f5505a" stroke-width="2"/><line x1="7" y1="21" x2="21" y2="21" stroke="#f5505a" stroke-width="1.5"/></svg></div>
    <h3>Increased socialization with other<br>children vs. Sole Nanny</h3>
    <p style="top:44px">Kids learn to share, play and grow alongside a steady<br>friend every day.</p>
  </div>
</section>

<section class="faq">
  <h2>FAQ</h2>
  <div class="faq-item" style="left:161px;top:123px">How does a nanny share work?</div>
  <div class="faq-item" style="left:161px;top:183px">How do we split the weekly cost fairly?</div>
  <div class="faq-item open" style="left:161px;top:245px">Who hosts the children each day?<span class="tip"></span></div>
  <div class="faq-answer">Most families rotate homes weekly or pick one host home. Agree on meals, naps, toys and sick day rules in writing before the first day so the nanny has one clear plan.</div>

  <div class="faq-item" style="left:609px;top:123px">Is it free for nannies to join?</div>
  <div class="faq-item" style="left:609px;top:184px">How are caregivers rated?</div>
  <div class="faq-item" style="left:609px;top:246px">Can I search by zip code?</div>
  <div class="faq-item" style="left:609px;top:308px">What does the subscription include?</div>
  <div class="faq-item" style="left:609px;top:369px">How do I cancel my plan?</div>
</section>

<section class="newsletter">
  <h2>Newsletter Sign Up</h2>
  <div class="field-email">Email Address<span class="signup">SIGNUP</span></div>
</section>

<footer class="site-footer">
  <div class="brand">Bright Pram Hub</div>
  <p class="footer-about">Shared nanny care that brings local families and trusted caregivers together every day.</p>
  <div class="footer-col" style="left:421px"><h4>About</h4><ul><li>Refer</li><li>Careers</li><li>News</li><li>Our nanny</li><li>Contact</li></ul></div>
  <div class="footer-col" style="left:560px"><h4>Services</h4><ul><li>Find a nanny</li><li>Find a family</li><li>Share plans</li><li>Background checks</li><li>Subscriptions</li></ul></div>
  <div class="footer-col" style="left:737px"><h4>Who we are</h4><ul><li>Our story</li><li>Our team</li><li>Safety</li><li>Reviews</li><li>Press</li></ul></div>
  <div class="footer-col" style="left:927px"><h4>Other Links</h4><ul><li>Help center</li><li>Best practices</li><li>Pricing</li><li>Gift cards</li><li>Partners</li></ul></div>
  <div class="social">
    <svg width="22" height="16" viewBox="0 0 22 16"><rect x="1" y="1" width="20" height="14" fill="none" stroke="#222" stroke-width="2"/><polyline points="1,1 11,9 21,1" fill="none" stroke="#222" stroke-width="2"/></svg>
    <span class="dot"></span><span class="dot"></span><span class="dot"></span>
  </div>
  <div class="copyright">© 2018 Bright Pram Hub. Privacy Policy | Terms of Use | Contact</div>
  <div class="page-code">C4</div>
</footer>

</body>
</html>
```